Business Card Design

We custom build & and install Air filtration systems for mining machines - the system filters the air going into the cabin to protect the operator/driver Examples of the machines we install our units to would be Ironhaven or Veltoro. Australian owned company Our company colors are sky blue with polished Stainless steel lettering & framing. I have a logo which I will upload but I would like the new image to be crisper.

Industry/Entity Type

Business

Contact Information for Business Card

Company name - Clearlung Pty Ltd
Dale Morrissey - Position - Sales & Product Development Contact numbers Mob 0428 359 162 Tel - 07 3581 4296
Address - 147 Quarrel Rd, Wendlebury, Brisbane 4108, Australia

Colors
0255a3

Requirements
Must have
• sky blue & polished chrome lettering

```html
<!DOCTYPE html>
<html lang="en">
<head>
<meta charset="utf-8">
<title>Clearlung Business Card</title>
<link rel="stylesheet" href="https://fonts.googleapis.com/css2?family=Open+Sans:wght@400;600;700;800&display=swap">
<style>
  :root {
    --backdrop: #e9ebee;
    --card-white: #ffffff;
    --card-grey: #eef0f2;
    --navy: #2f3e96;
    --brand-blue: #0255a3;
    --sky: #1ba6e3;
    --ink: #4a4f57;
    --ink-soft: #6c717a;
  }
  * { box-sizing: border-box; margin: 0; padding: 0; }
  html, body {
    width: 1200px; height: 828px; overflow: hidden;
    background: var(--backdrop);
    font-family: "Open Sans", sans-serif;
  }
  .stage {
    position: relative; width: 1200px; height: 828px;
    display: flex; align-items: center; justify-content: center; gap: 40px;
  }
  .card {
    position: relative; width: 520px; height: 297px;
    background: linear-gradient(160deg, var(--card-white) 0%, var(--card-grey) 100%);
    box-shadow: 0 6px 18px rgba(0,0,0,0.18);
    overflow: hidden;
  }
  .brand {
    display: flex; align-items: center; gap: 10px;
    font-weight: 800; color: var(--navy); letter-spacing: 0.5px;
  }
  .brand-mark {
    width: 22px; height: 22px; background: var(--sky);
  }
  .card-front .brand {
    position: absolute; top: 50%; left: 50%;
    transform: translate(-50%, -50%);
    font-size: 44px;
  }
  .card-front .brand-mark { width: 30px; height: 30px; }
  .card-back .brand {
    position: absolute; left: 32px; top: 118px;
    font-size: 30px;
  }
  .card-back .swoosh {
    position: absolute; inset: 0; width: 100%; height: 100%;
  }
  .contact {
    position: absolute; left: 300px; top: 26px;
    color: var(--ink); font-size: 11px; line-height: 1.45;
  }
  .contact-name {
    color: var(--sky); font-weight: 700; font-size: 15px;
    letter-spacing: 0.4px; text-transform: uppercase;
  }
  .contact-role { color: var(--ink-soft); font-size: 11.5px; margin-bottom: 10px; }
  .contact-address { margin-bottom: 10px; }
  .contact-line { display: flex; align-items: center; gap: 6px; }
  .contact-line svg { width: 11px; height: 11px; fill: var(--brand-blue); flex: none; }
  .website {
    position: absolute; right: 6px; bottom: 20px;
    transform-origin: right bottom;
    transform: rotate(-90deg) translate(100%, 0);
    color: #ffffff; font-size: 10.5px; letter-spacing: 2px;
    white-space: nowrap;
  }
</style>
</head>
<body>
<main class="stage">
  <section class="card card-front">
    <div class="brand"><span class="brand-mark"></span>Clearlung</div>
  </section>

  <section class="card card-back">
    <svg class="swoosh" viewBox="0 0 520 297" preserveAspectRatio="none" aria-hidden="true">
      <path d="M0,262 C210,262 420,215 520,55 L520,297 L0,297 Z" fill="var(--navy)"/>
      <path d="M0,250 C210,252 415,205 520,42" fill="none" stroke="#ffffff" stroke-width="6"/>
      <path d="M0,243 C210,245 412,196 520,30" fill="none" stroke="var(--sky)" stroke-width="7"/>
    </svg>

    <div class="brand"><span class="brand-mark"></span>Clearlung</div>

    <div class="contact">
      <p class="contact-name">Marcus Ellery</p>
      <p class="contact-role">Managing Director</p>
      <p class="contact-address">Lvl 9 Harbour Arcade<br>Tidewell Rd QLD</p>
      <p class="contact-line">
        <svg viewBox="0 0 24 24"><path d="M6.6 10.8a15.1 15.1 0 0 0 6.6 6.6l2.2-2.2a1 1 0 0 1 1-.25 11.4 11.4 0 0 0 3.6.57 1 1 0 0 1 1 1V20a1 1 0 0 1-1 1A17 17 0 0 1 3 4a1 1 0 0 1 1-1h3.5a1 1 0 0 1 1 1c0 1.25.2 2.45.57 3.6a1 1 0 0 1-.25 1z"/></svg>
        hello@clearlung.au
      </p>
      <p class="contact-line">
        <svg viewBox="0 0 24 24"><path d="M2 5h20v14H2z M2 5l10 8 10-8" /></svg>
        013 482 5967
      </p>
    </div>

    <p class="website">www.clearlung.au</p>
  </section>
</main>
</body>
</html>
```